Vantiqo custom business card design

Need a authentic, innovative business card design for a new mobile app business. I am uploading a few screen images from our app for you to view. I would like app design theme to match business card design. I can also send logo images.

```html
<!DOCTYPE html>
<html lang="en">
<head>
<meta charset="UTF-8">
<title>Vantiqo Business Card</title>
<link href="https://fonts.googleapis.com/css2?family=Work+Sans:wght@400;500;700&display=swap" rel="stylesheet">
<style>
  :root {
    --bg: #161616;
    --card: #262626;
    --card-light: #2e2e2e;
    --purple: #6a35a0;
    --white: #ffffff;
    --text: #f1f1f1;
  }
  * { margin: 0; padding: 0; box-sizing: border-box; }
  html, body { width: 1200px; height: 900px; overflow: hidden; }
  body {
    background: var(--bg);
    font-family: "Work Sans", sans-serif;
    display: flex;
    flex-direction: column;
    align-items: center;
    justify-content: center;
    gap: 36px;
  }
  .card {
    position: relative;
    width: 660px;
    height: 378px;
    background: radial-gradient(circle at 75% 55%, var(--card-light), var(--card) 70%);
    border-bottom: 5px solid var(--purple);
  }
  .card--front {
    display: flex;
    flex-direction: column;
    align-items: center;
    justify-content: center;
    gap: 22px;
  }
  .brand-dot {
    width: 120px;
    height: 120px;
    border-radius: 50%;
    background: var(--purple);
  }
  .brand-name {
    font-weight: 700;
    font-size: 46px;
    color: var(--white);
    letter-spacing: 1px;
  }
  .card--back {
    display: flex;
    align-items: center;
    justify-content: center;
    gap: 28px;
  }
  .identity {
    text-align: right;
    color: var(--text);
    font-size: 19px;
    line-height: 1.3;
    letter-spacing: 1px;
  }
  .identity__name {
    color: var(--purple);
    font-size: 27px;
    font-weight: 500;
    text-transform: uppercase;
    letter-spacing: 1.5px;
  }
  .divider {
    width: 2px;
    height: 112px;
    background: var(--purple);
  }
  .contacts {
    list-style: none;
    color: var(--text);
    font-size: 19px;
    line-height: 1.45;
    letter-spacing: 1.2px;
  }
  .contacts li { display: flex; align-items: center; gap: 12px; }
  .contacts svg {
    width: 14px; height: 14px;
    fill: none; stroke: var(--purple); stroke-width: 1.6;
  }
</style>
</head>
<body>
  <section class="card card--front">
    <div class="brand-dot"></div>
    <div class="brand-name">Vantiqo</div>
  </section>

  <section class="card card--back">
    <div class="identity">
      <div class="identity__name">Daniel Reyes</div>
      <div>Director</div>
      <div>2725 Harbor Lane</div>
      <div>Clearwater, FL 33755</div>
    </div>
    <div class="divider"></div>
    <ul class="contacts">
      <li><svg viewBox="0 0 14 14"><rect x="3.5" y="1" width="7" height="12" rx="1"/><line x1="6" y1="11" x2="8" y2="11"/></svg>(555) 318-4207</li>
      <li><svg viewBox="0 0 14 14"><path d="M3 1.5 L5.5 1.5 L6.5 4.5 L5 5.8 Q6.5 8.5 8.5 9.2 L9.8 7.6 L12.5 8.6 L12.5 11 Q12 12.5 10.5 12.5 Q2 11 1.5 3.5 Q1.5 1.8 3 1.5 Z"/></svg>(555) 604-9172</li>
      <li><svg viewBox="0 0 14 14"><rect x="1" y="3" width="12" height="8.5"/><polyline points="1,3 7,8 13,3"/></svg>info@vantiqo.com</li>
      <li><svg viewBox="0 0 14 14"><circle cx="7" cy="7" r="5.8"/><ellipse cx="7" cy="7" rx="2.6" ry="5.8"/><line x1="1.2" y1="7" x2="12.8" y2="7"/></svg>www.vantiqo.com</li>
    </ul>
  </section>
</body>
</html>
```